Custom Beer Labelling Company Needs a Flyer

We need a flyer designed to promote Hopwrapz, a new company in Sydney that helps home brewers create their own small batch beer labels. Main purpose of the flyer is to increase awareness of the service we offer and drive traffic to the Hopwrapz shopify site - www.hopwrapz-demo.com.au.
Our value proposition is about being easy (less than 5 minutes), affordable (full set of labels from only $12) with good quality (water resistant synthetic labels that remove cleanly).
The flyer should suit A4 printing and will preferably include screenshot of the "Create your Label" tool on the site, and/or examples of our label templates. It may also include other information from our site such eg from the "About Us" or About Our Labels" pages.

Target Market(s)

Home brewers, mostly males aged 20-50

Industry/Entity Type

It Company

Colors
ec1f27
fee3d4
f9ba93
f68d4e
f37122
f78f20
faa54b
fbc994
ffffff

Requirements
Must have
• Drive customers to www.hopwrapz-demo.com as call to action
Nice to have
• screenshot(s) and examples of labels

```html
<!DOCTYPE html>
<html lang="en">
<head>
<meta charset="utf-8">
<title>Hopwrapz Flyer</title>
<link href="https://fonts.googleapis.com/css2?family=Jost:wght@400;500;700&family=Bree+Serif&family=Roboto+Slab:wght@700&display=swap" rel="stylesheet">
<style>
  :root {
    --red: #ec1f27;
    --cream: #fdf0cf;
    --cream-deep: #f8dfb4;
    --peach: #f9ba93;
    --orange: #f78f20;
    --orange-soft: #faa54b;
    --orange-dark: #f37122;
    --rust: #c8692a;
    --band: #cf7834;
    --brown: #5a3215;
    --ink: #1d1d1d;
    --white: #ffffff;
    --label-red: #8e1a22;
  }
  * { box-sizing: border-box; margin: 0; padding: 0; }
  html, body { width: 1041px; height: 1200px; overflow: hidden; }
  body { background: #ebe7e4; position: relative; font-family: "Jost", sans-serif; }

  .flyer {
    position: absolute; left: 95px; top: 0; width: 850px; height: 1200px;
    background: var(--cream); overflow: hidden;
  }
  .flyer-texture {
    position: absolute; inset: 0;
    background: radial-gradient(ellipse at 50% 40%, #fef5dc 0%, var(--cream) 55%, var(--cream-deep) 100%);
  }

  .brand { position: absolute; top: 48px; left: 0; width: 100%; display: flex; justify-content: center; align-items: center; gap: 18px; }
  .brand-mark { width: 92px; height: 92px; background: var(--orange); }
  .brand-name { font-family: "Jost", sans-serif; font-weight: 700; font-size: 96px; line-height: 1; color: var(--orange); letter-spacing: 1px; }
  .brand-tag { position: absolute; top: 160px; left: 275px; font-family: "Roboto Slab", serif; font-size: 26px; color: var(--rust); letter-spacing: 2px; }

  .line { position: absolute; left: 0; width: 100%; text-align: center; white-space: nowrap; }
  .intro { top: 204px; font-size: 31px; font-weight: 500; color: var(--ink); }
  .url-main { top: 250px; font-size: 44px; font-weight: 700; color: var(--red); }
  .pitch-a { top: 306px; font-family: "Bree Serif", serif; font-size: 37px; color: var(--rust); letter-spacing: 1px; }
  .pitch-b { top: 346px; font-family: "Bree Serif", serif; font-size: 56px; color: var(--orange); letter-spacing: 2px; }
  .pitch-c { top: 408px; font-size: 35px; font-weight: 500; color: var(--rust); letter-spacing: 1px; }
  .slogan { top: 466px; font-size: 28px; font-weight: 500; color: var(--ink); }

  .laptop-lid { position: absolute; left: 129px; top: 511px; width: 592px; height: 395px; background: #111; border-radius: 22px 22px 0 0; border: 2px solid #9a9a9a; }
  .laptop-screen { position: absolute; left: 160px; top: 541px; width: 528px; height: 334px; background: #f1f0ee; overflow: hidden; }
  .laptop-name { position: absolute; left: 0; top: 887px; width: 850px; text-align: center; font-size: 10px; color: #9a9a9a; }
  .laptop-base { position: absolute; left: 38px; top: 906px; width: 774px; height: 38px; background: linear-gradient(#e6e6e6, #b9b9b9 60%, #8d8d8d); border-radius: 4px 4px 40px 40px / 4px 4px 30px 30px; }
  .laptop-notch { position: absolute; left: 365px; top: 906px; width: 120px; height: 8px; background: #a9a9a9; border-radius: 0 0 8px 8px; }

  .site-head { position: absolute; left: 0; top: 0; width: 100%; height: 40px; background: var(--white); display: flex; align-items: center; justify-content: space-between; padding: 0 10px; }
  .site-logo { display: flex; align-items: center; gap: 5px; font-size: 19px; font-weight: 500; color: var(--brown); }
  .site-logo span { width: 14px; height: 14px; background: var(--orange); }
  .site-nav { display: flex; gap: 8px; font-size: 6.5px; letter-spacing: 1px; color: #777; }

  .label-panel { position: absolute; left: 4px; top: 42px; width: 248px; height: 288px; background: linear-gradient(90deg, #3b0c10, var(--label-red) 30%, var(--label-red) 70%, #3b0c10); }
  .label-preview { position: absolute; left: 28px; top: 28px; width: 192px; height: 178px; background: linear-gradient(#fbf3ef, #f4d8da); border: 3px solid #b1242e; }
  .thumbs { position: absolute; left: 26px; top: 236px; display: flex; gap: 6px; }
  .thumbs span { width: 32px; height: 32px; border: 2px solid #fff; }

  .form { position: absolute; left: 262px; top: 50px; width: 256px; }
  .form h2 { font-size: 14px; font-weight: 500; color: #333; }
  .form .sub { font-size: 7px; color: #666; margin-bottom: 6px; }
  .grid { display: grid; grid-template-columns: 1fr 1fr; gap: 3px 10px; }
  .grid.three { grid-template-columns: 1fr 1fr 1fr; }
  .field label { display: block; font-size: 6px; font-weight: 700; letter-spacing: .6px; color: #555; }
  .field div { height: 14px; background: var(--white); border: 1px solid #ccc; font-size: 7.5px; padding: 1px 3px; color: #444; }
  .notes { margin-top: 3px; }
  .notes div { height: 26px; line-height: 1.3; }
  .opts { display: flex; gap: 10px; margin-top: 4px; }
  .swatches { display: flex; gap: 2px; }
  .swatches i { width: 15px; height: 11px; display: block; }
  .icons, .btype { display: flex; background: var(--white); border: 1px solid #ccc; height: 13px; align-items: center; font-size: 7px; }
  .icons b { width: 14px; text-align: center; font-weight: 400; }
  .btype span { padding: 0 7px; }
  .btype span:first-child { background: #ddd; }
  .buy { display: flex; align-items: center; gap: 46px; margin-top: 10px; padding-left: 34px; }
  .price { font-size: 13px; color: #555; }
  .add { background: var(--red); color: #fff; font-size: 8px; padding: 4px 8px; }

  .features { position: absolute; left: 0; top: 970px; width: 850px; height: 128px; background: var(--band); }
  .features svg { position: absolute; left: 0; top: 0; }
  .feature { position: absolute; top: 22px; font-size: 16.5px; line-height: 1.3; color: var(--white); }
  .feature.one { left: 40px; width: 230px; }
  .feature.two { left: 307px; width: 212px; top: 32px; }
  .feature.three { left: 557px; width: 260px; text-align: justify; }

  .cta { position: absolute; left: 0; top: 1103px; width: 850px; height: 97px; background: linear-gradient(var(--orange), var(--orange-dark)); text-align: center; color: var(--white); padding-top: 12px; }
  .cta p { font-size: 25px; font-weight: 500; }
  .cta .url { font-size: 29px; margin-top: 2px; }
</style>
</head>
<body>
<main class="flyer">
  <div class="flyer-texture" role="img" aria-label="Faint background pattern of beer label templates"></div>

  <div class="brand">
    <div class="brand-mark"></div>
    <div class="brand-name">Hopwrapz</div>
  </div>
  <div class="brand-tag">BEST HOMEBREW LABELS</div>

  <p class="line intro">Easy &amp; Affordable Small Batch Beer Labels At</p>
  <p class="line url-main">www.hopwrapz-demo.com.au</p>
  <p class="line pitch-a">LESS THAN FIVE MINUTES AND</p>
  <p class="line pitch-b">FROM JUST $12 FOR</p>
  <p class="line pitch-c">A FULL SET OF CUSTOM PRINTED LABELS.</p>
  <p class="line slogan">Take Your Homebrew To Another Level.</p>

  <div class="laptop-lid"></div>
  <section class="laptop-screen">
    <header class="site-head">
      <div class="site-logo"><span></span>Hopwrapz</div>
      <nav class="site-nav"><span>CREATE YOUR LABEL</span><span>ABOUT US</span><span>ABOUT OUR LABELS</span><span>BLOG</span></nav>
    </header>
    <div class="label-panel">
      <div class="label-preview" role="img" aria-label="Preview of a red beer label template reading Your Beer, Beer Style"></div>
      <div class="thumbs">
        <span style="background:#b1242e"></span><span style="background:#222"></span><span style="background:#c8b98a"></span><span style="background:#5aa8a0"></span><span style="background:#cbbf8f"></span>
      </div>
    </div>
    <div class="form">
      <h2>CREATE YOUR LABEL</h2>
      <p class="sub">easy and affordable small batch beer labels</p>
      <div class="grid">
        <div class="field"><label>BEER NAME</label><div>Your Beer</div></div>
        <div class="field"><label>STYLE</label><div>Beer Style</div></div>
        <div class="field"><label>BREWED BY</label><div>Your Brewery</div></div>
        <div class="field"><label>TAGLINE</label><div>Your Tagline</div></div>
      </div>
      <div class="grid three">
        <div class="field"><label>BREWED</label><div>08/05/16</div></div>
        <div class="field"><label>BOTTLED</label><div>18/05/16</div></div>
        <div class="field"><label>ABV</label><div>0.0%</div></div>
      </div>
      <div class="grid">
        <div class="field"><label>ORIGINAL GRAVITY</label><div>1.010</div></div>
        <div class="field"><label>FINAL GRAVITY</label><div>1.010</div></div>
      </div>
      <div class="field notes"><label>NOTES</label><div>This may include further brewing details such as grain bill, mash and sparge temperatures, boil time and hop additions</div></div>
      <div class="opts">
        <div class="field"><label>COLOR</label><div class="swatches" style="border:0;background:none;padding:0"><i style="background:#111"></i><i style="background:#c8b98a"></i><i style="background:#5aa8a0"></i><i style="background:#b1242e"></i></div></div>
        <div class="field"><label>ICON</label><div class="icons"><b>⚓</b><b>♔</b><b>✲</b></div></div>
        <div class="field"><label>BOTTLE TYPE</label><div class="btype"><span>Large</span><span>Small</span></div></div>
      </div>
      <div class="buy"><span class="price">$0.79</span><span class="add">ADD</span></div>
    </div>
  </section>
  <p class="laptop-name">Lumabook</p>
  <div class="laptop-base"></div>
  <div class="laptop-notch"></div>

  <section class="features">
    <svg width="850" height="128" viewBox="0 0 850 128" aria-hidden="true">
      <polyline points="276,0 290,64 276,128" fill="none" stroke="#ffffff" stroke-width="3"/>
      <polyline points="526,0 540,64 526,128" fill="none" stroke="#ffffff" stroke-width="3"/>
    </svg>
    <p class="feature one">Just fill in template with details of your brew, and select from our range of designs, colours, icons and bottle size.</p>
    <p class="feature two">We print your labels in high quality LED on A4 sheets of die cut, self-adhesive labels</p>
    <p class="feature three">Our synthetic labels are water resistant and remove cleanly from your empties without tearing and without leftover glue crud.</p>
  </section>

  <footer class="cta">
    <p>Try A Set Of Hopwrapz Next Time You Lay Down A Batch.</p>
    <p class="url">www.hopwrapz-demo.com.au</p>
  </footer>
</main>
</body>
</html>
```